Velmoria-Quillmesh Partial Redesign - Web App

Are you able to apply your creativity to an existing layout? I’m convinced that even just a few touches can make a big difference to add personality and professionalism to a website design, and I’m looking for someone able to use existing ideas and bring them to the next level while keeping inside some given constraints.
The actual job is to improve an existing design concept and to apply it creatively to a landing page, a simple home page, and an older web app (single page website).
To help you start with a clear picture of the current situation and of my requirements, I created a detailed brief with screenshots, live examples, and complete instructions. You can find it attached to this job.
My tastes are inclined towards clean and simple designs. For this project I'm not looking for dazzling novelty, but for very solid craftsmanship. Are the right man - or woman - for the job?
Updates
I wanted to thank everybody who participated in this project. I made a choice, but also other designs were interesting. Hope to work with you another time.
Target Market(s)
Our main target is social media marketers and startuppers
Look and feel
Each slider illustrates characteristics of the customer's brand and the style your logo design should communicate.

```html
<!DOCTYPE html>
<html lang="en">
<head>
<meta charset="utf-8">
<title>Velmoria – Hashtag Summary</title>
<link rel="stylesheet" href="https://fonts.googleapis.com/css2?family=Arimo:ital,wght@0,400;0,700;1,400&family=Gelasio:wght@400&display=swap">
<style>
:root{
  --bar-top:#363636;
  --bar-bottom:#161616;
  --btn:#3c3c3c;
  --btn-border:#555;
  --text:#222;
  --link:#2a86c8;
  --panel:#f3f3f3;
  --line:#dcdcdc;
  --heading-bar:#a2abaf;
  --white:#fff;
  --red:#dd3c1a;
  --orange:#ff9a00;
  --green:#139a1c;
  --needle:#e8674a;
  --hub:#4a86e8;
}
*{box-sizing:border-box;margin:0;padding:0}
html,body{width:1200px;height:1032px;overflow:hidden;background:var(--white)}
body{font-family:"Arimo",Arial,sans-serif;color:var(--text)}
.stage{width:1020px;height:877px;transform:scale(1.17647);transform-origin:0 0;position:relative}

.topbar{position:absolute;left:0;top:0;width:1020px;height:51px;background:linear-gradient(var(--bar-top),var(--bar-bottom));}
.brand{position:absolute;left:44px;top:15px;display:flex;align-items:center;gap:8px;color:var(--white);font-weight:700;font-size:16px}
.brand-mark{width:18px;height:18px;border-radius:50%;background:#8a8a8a}
.nav-btn{position:absolute;top:12px;height:31px;border-radius:3px;background:var(--btn);border:1px solid var(--btn-border);color:#eee;font-size:14px;display:flex;align-items:center;justify-content:center;gap:6px}
.nav-home{left:201px;width:49px;background:#0d0d0d;border-color:#2a2a2a}
.nav-products{left:259px;width:86px}
.nav-blog{left:698px;width:50px}
.nav-about{left:756px;width:49px}
.nav-help{left:813px;width:48px}
.account{position:absolute;left:890px;top:18px;color:#eee;font-size:14px;display:flex;align-items:center;gap:10px}
.account-pointer{position:absolute;left:930px;top:51px;width:0;height:0;border-left:6px solid transparent;border-right:6px solid transparent;border-top:6px solid #1a1a1a}

.page-title{position:absolute;left:46px;top:103px;font-size:24px;font-weight:400}
.page-title a{color:var(--link);text-decoration:none}
.tracked{position:absolute;left:46px;top:138px;font-size:12px;font-style:italic}
.tracked a{color:var(--link);text-decoration:none}

.tabs{position:absolute;left:645px;top:162px;display:flex;gap:3px}
.tab{height:32px;padding:0 10px;display:flex;align-items:center;font-size:13px;background:#e2e2e2;border:1px solid var(--line);border-bottom:none;border-radius:4px 14px 0 0}
.tab.active{background:var(--panel);padding:0 14px}

.panel{position:absolute;left:30px;top:193px;width:960px;height:700px;background:var(--panel);border:1px solid var(--line);border-radius:4px}

.stats{position:absolute;left:40px;top:248px;width:940px;height:72px;display:flex}
.stat{display:flex;flex-direction:column;align-items:center;justify-content:center;border-right:1px solid var(--line)}
.stat:last-child{border-right:none}
.stat-value{font-family:"Gelasio",Georgia,serif;font-size:22px}
.stat-label{font-size:12px;font-style:italic;margin-top:4px}
.stat.link .stat-value,.stat.link .stat-label{color:var(--link)}

.bar{position:absolute;height:32px;background:var(--heading-bar);color:var(--white);border-radius:4px;display:flex;align-items:center;justify-content:center}
.bar-main{left:40px;top:383px;width:940px;font-size:20px}
.bar-sub{top:438px;width:460px;font-size:16px}
.gauge-card{position:absolute;top:478px;width:460px;height:375px;background:var(--white);border:1px solid var(--line);border-radius:4px}
.left{left:40px}.right{left:520px}
.gauge{display:block}
</style>
</head>
<body>
<div class="stage">
  <header class="topbar">
    <div class="brand"><span class="brand-mark"></span>Velmoria</div>
    <div class="nav-btn nav-home">
      <svg width="14" height="13" viewBox="0 0 14 13"><path d="M7 0 L14 6 H12 V13 H8.5 V9 H5.5 V13 H2 V6 H0 Z" fill="#fff"/></svg>
    </div>
    <div class="nav-btn nav-products">Products <svg width="8" height="5" viewBox="0 0 8 5"><path d="M0 0H8L4 5Z" fill="#eee"/></svg></div>
    <div class="nav-btn nav-blog">Blog</div>
    <div class="nav-btn nav-about">About</div>
    <div class="nav-btn nav-help">Help</div>
    <div class="account">
      <svg width="14" height="14" viewBox="0 0 14 14"><circle cx="7" cy="4" r="3.5" fill="#fff"/><path d="M0 14 Q0 8 7 8 Q14 8 14 14Z" fill="#fff"/></svg>
      Account
    </div>
  </header>
  <div class="account-pointer"></div>

  <h1 class="page-title">Hashtag: <a href="#">#socialtips</a></h1>
  <p class="tracked">Tracked influencers: <a href="#">@marcusvale</a>, <a href="#">@crimsonleafmedia</a></p>

  <nav class="tabs">
    <span class="tab active">Summary</span>
    <span class="tab">Timeline</span>
    <span class="tab">Influencers</span>
    <span class="tab">Hashtags</span>
  </nav>

  <section class="panel"></section>

  <div class="stats">
    <div class="stat" style="width:186px"><span class="stat-value">8</span><span class="stat-label">Observed Days</span></div>
    <div class="stat link" style="width:209px"><span class="stat-value">8,492,949</span><span class="stat-label">Total Impressions</span></div>
    <div class="stat link" style="width:164px"><span class="stat-value">843</span><span class="stat-label">Total Tweets</span></div>
    <div class="stat" style="width:211px"><span class="stat-value">1,061,619</span><span class="stat-label">Daily Impressions</span></div>
    <div class="stat" style="width:170px"><span class="stat-value">105</span><span class="stat-label">Daily Tweets</span></div>
  </div>

  <div class="bar bar-main">TREND ANALYSIS</div>
  <div class="bar bar-sub left">Trend With Your Influencers</div>
  <div class="bar bar-sub right">Trend Without Your Influencers</div>

  <div class="gauge-card left">
    <svg class="gauge" width="458" height="373" viewBox="0 0 458 373">
      <defs>
        <g id="trend-gauge" font-family="Arimo, Arial, sans-serif">
          <circle cx="218" cy="192" r="134" fill="#cfcfcf" stroke="#9a9a9a"/>
          <circle cx="218" cy="192" r="125" fill="#f4f4f4" stroke="#e6e6e6"/>
          <path d="M147.3 262.7 A100 100 0 0 1 153.7 115.4" fill="none" stroke="var(--red)" stroke-width="27"/>
          <path d="M153.7 115.4 A100 100 0 0 1 282.3 115.4" fill="none" stroke="var(--orange)" stroke-width="27"/>
          <path d="M282.3 115.4 A100 100 0 0 1 288.7 262.7" fill="none" stroke="var(--green)" stroke-width="27"/>
          <g stroke="#333" stroke-width="2">
            <line x1="138.1" y1="271.9" x2="156.5" y2="253.5"/>
            <line x1="113.6" y1="148.8" x2="131.7" y2="156.3"/>
            <line x1="218" y1="79" x2="218" y2="99"/>
            <line x1="322.4" y1="148.8" x2="304.3" y2="156.3"/>
            <line x1="297.9" y1="271.9" x2="279.5" y2="253.5"/>
          </g>
          <text x="218" y="163" text-anchor="middle" font-size="28" fill="#333">Trend</text>
          <text x="176" y="258" text-anchor="middle" font-size="15" fill="#333">-100</text>
          <text x="264" y="258" text-anchor="middle" font-size="15" fill="#333">100</text>
          <text x="218" y="289" text-anchor="middle" font-size="28" fill="#111">3</text>
          <polygon points="218,85 222,192 218,228 214,192" fill="var(--needle)" stroke="#b84a33" transform="rotate(4 218 192)"/>
          <circle cx="218" cy="192" r="17" fill="var(--hub)" stroke="#3a6fc4"/>
        </g>
      </defs>
      <use href="#trend-gauge"/>
    </svg>
  </div>
  <div class="gauge-card right">
    <svg class="gauge" width="458" height="373" viewBox="0 0 458 373"><use href="#trend-gauge"/></svg>
  </div>
</div>
</body>
</html>
```